Brightfield Program (8 x 8) to be posted on Facebook, Twitter & Instagram

YOUR NEW HOME PURCHASE IS BRIGHTFIELD BOUND
with the
HLB BRIGHTFIELD 2.0 PROGRAM
* Up to 5% Assistance with 640 Score
* Up to 6% Assistance with 660 Score
* Also 6% Seller Help Allowed
Call to be Pre-Qualified Today!
(800) 417-2960
Copperline Financial Services, Inc.
7120 Marlow Brook Road, Harwick Springs, MD 20917
www.copperlinelending.com
LRID #731586

```html
<!DOCTYPE html>
<html lang="en">
<head>
<meta charset="utf-8">
<title>Brightfield Program</title>
<link href="https://fonts.googleapis.com/css2?family=Montserrat:wght@400;500;700;800;900&family=Bebas+Neue&display=swap" rel="stylesheet">
<style>
  :root {
    --brand-blue: #0f66b0;
    --ink: #2f2a2a;
    --gold: #b9a24c;
    --white: #ffffff;
    --black: #111111;
  }
  html, body { margin: 0; padding: 0; overflow: hidden; background: var(--white); }
  .ad {
    position: relative;
    width: 1200px; height: 1200px;
    overflow: hidden;
    background: var(--white);
    font-family: 'Montserrat', sans-serif;
  }
  .hero-photo {
    position: absolute; left: 0; top: 0; width: 1200px; height: 789px;
    background:
      linear-gradient(90deg, rgba(255,255,255,0) 0%, rgba(255,255,255,0) 52%, rgba(255,255,255,0.75) 72%, #ffffff 96%),
      linear-gradient(180deg, #5f6f8c 0%, #6b7a96 35%, #8a8f9c 60%, #5f8a3c 68%, #4f7d2f 100%);
  }
  .headline {
    position: absolute; left: 640px; width: 460px; top: 0; height: 789px;
    text-align: center; margin: 0;
  }
  .headline span { display: block; position: absolute; left: -60px; right: -60px; white-space: nowrap; line-height: 1; }
  .hl-your { top: 282px; font-size: 54px; font-weight: 900; color: var(--ink); }
  .hl-big { font-size: 88px; font-weight: 900; color: var(--brand-blue); letter-spacing: -2px; }
  .hl-new { top: 340px; }
  .hl-purchase { top: 423px; }
  .hl-bound { top: 513px; font-size: 42px; font-weight: 900; color: var(--ink); letter-spacing: -1px; }
  .hl-with { top: 580px; font-size: 30px; font-weight: 800; color: var(--ink); }
  .hl-program-name { top: 627px; font-size: 42px; font-weight: 900; color: var(--brand-blue); letter-spacing: -0.5px; }
  .hl-program { top: 672px; font-size: 68px; font-weight: 900; color: var(--brand-blue); letter-spacing: -2px; }

  .benefits {
    position: absolute; left: 0; top: 789px; width: 1200px; height: 121px;
    background: var(--brand-blue);
    display: flex; align-items: center;
  }
  .benefit {
    flex: 1; text-align: center; color: var(--white);
    font-family: 'Bebas Neue', sans-serif; font-size: 46px; line-height: 0.98;
  }
  .benefit-divider { width: 2px; height: 76px; background: rgba(255,255,255,0.85); }

  .brand-mark {
    position: absolute; left: 52px; top: 1024px; width: 330px;
    display: flex; align-items: center; gap: 14px;
    color: var(--brand-blue); font-weight: 800; font-size: 24px; line-height: 1.15;
  }
  .brand-dot { width: 44px; height: 44px; border-radius: 50%; background: var(--gold); flex: none; }

  .cta-pill {
    position: absolute; left: 456px; top: 935px; width: 402px; height: 39px;
    border-radius: 19px; background: var(--gold); color: var(--white);
    font-size: 22px; font-weight: 500; text-align: center; line-height: 39px; letter-spacing: 0.5px;
  }
  .phone {
    position: absolute; left: 400px; width: 486px; top: 986px; text-align: center;
    font-size: 64px; font-weight: 800; color: var(--brand-blue); letter-spacing: -1px; line-height: 1;
  }
  .website {
    position: absolute; left: 400px; width: 520px; top: 1052px; text-align: center;
    font-size: 28px; font-weight: 800; color: var(--gold); margin-left: -20px;
  }
  .company {
    position: absolute; left: 448px; top: 1114px; font-size: 23px; font-weight: 800; color: var(--black);
  }
  .address {
    position: absolute; left: 448px; top: 1147px; font-size: 19px; font-weight: 500; color: var(--black);
  }
  .housing-badge {
    position: absolute; left: 1000px; top: 964px; width: 140px; height: 140px; background: var(--black);
  }
  .license {
    position: absolute; left: 990px; width: 160px; top: 1144px; text-align: center;
    font-size: 17px; font-weight: 500; color: var(--black);
  }
</style>
</head>
<body>
<main class="ad">
  <div class="hero-photo" role="img" aria-label="Smiling family of five standing on a front lawn before a grey two-storey house, the father holding up a key"></div>

  <h1 class="headline">
    <span class="hl-your">YOUR</span>
    <span class="hl-big hl-new">NEW HOME</span>
    <span class="hl-big hl-purchase">PURCHASE</span>
    <span class="hl-bound">IS BRIGHTFIELD BOUND</span>
    <span class="hl-with">with the</span>
    <span class="hl-program-name">HLB BRIGHTFIELD</span>
    <span class="hl-program">2.0 PROGRAM</span>
  </h1>

  <section class="benefits">
    <div class="benefit">* UP TO 5% ASSISTANCE<br>WITH 640 SCORE</div>
    <div class="benefit-divider"></div>
    <div class="benefit">* UP TO 6% ASSISTANCE<br>WITH 660 SCORE</div>
    <div class="benefit-divider"></div>
    <div class="benefit">* ALSO 6% SELLER<br>HELP ALLOWED</div>
  </section>

  <div class="brand-mark"><span class="brand-dot"></span><span>Copperline<br>Financial Services, Inc.</span></div>

  <div class="cta-pill">Call to be Pre-Qualified Today!</div>
  <div class="phone">(800) 417-2960</div>
  <div class="website">www.copperlinelending.com</div>
  <div class="company">Copperline Financial Services, Inc.</div>
  <div class="address">7120 Marlow Brook Road, Harwick Springs, MD 20917</div>

  <div class="housing-badge" role="img" aria-label="Housing certification badge"></div>
  <div class="license">LRID #731586</div>
</main>
</body>
</html>
```